Flyer-Design für Karla Brettin
Zielgruppe
Ich bin psychologische Beraterin und Heilpraktikerin für Psychotherapie. Ich biete ein Coaching speziell für Mütter (meist Mütter mit neugeborenen Babys) an. Dieses Mütter-Coaching will ich bewerben. Die Flyer werden unter anderen an Ärzte und Hebammen weiter gegeben und dort in den Praxen ausliegen.
Aufgabenstellung
In meinem Logo herrschen die Farben orange und grau vor - es wäre schön, wenn sich diese Farben im Flyer wiederfinden würden - evtl. kombiniert mit mittelblau oder einem hellem grün.
Des weiteren möchte ich später Flyer im Din Lang Format (einseitig) mit anderen Angeboten erstellen. Das sollte mit dem Design dann auch möglich sein.
Der Schrifttyp soll bitte Arial sein, passend zum Logo. Ich habe bei Bildarro Fotos zu dem Thema erstanden, die ich stimmig finde. Diese Bilder sollten im Flyer genutzt werden.
Für diesen Flyer hätte ich gerne das Format: Falzblatt mit Wickelfalz - 279 x 219 mm

```html
<!DOCTYPE html>
<html lang="de">
<head>
<meta charset="utf-8">
<title>Flyer Coaching für Mütter – Karla Brettin</title>
<link href="https://fonts.googleapis.com/css2?family=Arimo:wght@400;700&family=Oswald:wght@300;400&display=swap" rel="stylesheet">
<style>
  :root{
    --orange:#e8901a;
    --orange-band:#f0a030;
    --grey-text:#6b6b6b;
    --dark-text:#2a2a2a;
    --panel-grey:#f2f1ef;
    --paper:#ffffff;
    --backdrop:#9bbcd8;
    --photo-a:#c9b5a6;
    --photo-b:#6f6560;
  }
  *{box-sizing:border-box;margin:0;padding:0}
  html,body{width:1200px;height:900px;overflow:hidden}
  body{background:var(--backdrop);font-family:"Arimo",Arial,sans-serif;color:var(--dark-text);position:relative}
  .spread{position:absolute;top:250px;width:582px;height:400px;background:var(--paper);display:flex;box-shadow:0 2px 6px rgba(0,0,0,.18)}
  .spread--outside{left:12px}
  .spread--inside{left:606px}
  .spread::before,.spread::after{content:"";position:absolute;left:0;right:0;height:12px;background:var(--orange-band);z-index:2}
  .spread::before{top:0}
  .spread::after{bottom:0}
  .panel{position:relative;width:194px;height:100%;padding:20px 8px 16px;font-size:6.3px;line-height:1.42}
  .panel--grey{background:var(--panel-grey)}
  .panel--center{text-align:center;color:var(--grey-text)}
  .why-box{background:var(--orange);color:#fff;font-weight:700;text-align:center;font-size:8.6px;line-height:1.55;padding:6px 4px;margin:4px -8px 8px -8px}
  .why-box .why-title{font-size:9.2px}
  .brand{text-align:center;margin-bottom:6px}
  .brand-name{display:inline-flex;align-items:center;gap:3px;color:var(--orange);font-size:14px;font-weight:400;letter-spacing:.2px}
  .brand-name .dot{width:6px;height:6px;border-radius:50%;background:var(--orange)}
  .brand-sub{color:var(--grey-text);font-weight:700;font-size:9.4px;margin-top:5px}
  .brand-claim{font-size:8.6px;color:var(--dark-text);margin-top:2px}
  .intro p{margin-bottom:7px}
  .contact{margin-top:76px;font-size:6.6px;line-height:1.6}
  .contact .name{font-size:8.6px;color:var(--dark-text)}
  .contact .gap{margin-top:6px}
  .services{margin-top:26px;font-size:6.4px;line-height:1.6}
  .services h3{font-size:6.6px;font-weight:700;color:var(--dark-text)}
  .quote{font-size:12.4px;line-height:1.35;color:var(--grey-text);text-align:center;margin-top:22px;padding:0 6px}
  .quote .mark{font-weight:700;font-size:12px;vertical-align:top;margin-right:4px}
  .photo{position:absolute;background:linear-gradient(135deg,var(--photo-a),var(--photo-b))}
  .photo--mother{left:0;right:0;top:143px;height:141px}
  .photo--tired{left:0;right:0;bottom:12px;height:118px}
  .brand--bottom{position:absolute;left:0;right:0;top:300px}
  .section-label{font-family:"Oswald",sans-serif;font-weight:300;font-size:8.4px;letter-spacing:.8px;color:var(--grey-text);text-transform:uppercase}
  .section-label em{font-style:normal;color:var(--orange);font-weight:400}
  .section-rule{width:24px;height:1px;background:#bdbdbd;margin:5px auto 8px}
  .bullets{list-style:none;color:var(--grey-text);margin-top:8px}
  .bullets li{margin-bottom:6px}
  .bullets li::before{content:"• "}
  .support h4{font-family:"Oswald",sans-serif;font-weight:400;font-size:7.4px;letter-spacing:.6px;color:var(--dark-text);margin:5px 0 4px}
  .support p{margin-bottom:5px}
  .way{color:var(--grey-text)}
  .way h3{font-family:"Oswald",sans-serif;font-weight:400;font-size:7.4px;letter-spacing:.5px;color:var(--dark-text);margin:10px 0 8px}
  .way p{margin-bottom:8px}
  .offer{display:flex;align-items:center;gap:3px;color:var(--orange);font-size:7.6px;margin:4px 0 3px}
  .offer svg{flex:none}
</style>
</head>
<body>

<section class="spread spread--outside" aria-label="Außenseite">
  <div class="panel panel--intro">
    <div class="why-box">
      <div class="why-title">Warum Coaching extra für Mütter?</div>
      <div>Nun:</div>
      <div>Nur wer gut für sich selbst sorgt,<br>kann auch für andere da sein!</div>
    </div>
    <div class="brand">
      <div class="brand-name"><span>karlabrettin</span><span class="dot"></span></div>
      <div class="brand-sub">Coaching für Mütter</div>
      <div class="brand-claim">Begleitung - Stärkung - Beratung</div>
    </div>
    <div class="intro">
      <p>Als geprüfte psychologische Beraterin und Heilpraktikerin für Psychotherapie habe ich mich besonders auf das Coaching für Mütter spezialisiert.</p>
      <p>Hier setze ich die Methode des lösungsorientierten Kurzzeitcoachings ein, die den Fokus auf Stärken und Lösungen und nicht auf Probleme und Hindernisse legt.</p>
      <p>Das Konzept wird durch Achtsamkeits- und Entspannungsübungen abgerundet. Aspekte der „gewaltfreien“ = wertschätzenden Kommunikation werden für individuelle Konfliktlösungen im familiären Alltag genutzt.<br>Starten Sie mit einem neuen und liebevollen Blick auf Ihr Leben und auf Ihre Fähigkeiten.</p>
      <p>Sie werden erstaunt sein, was alles in Ihnen wohnt.</p>
      <p>Versprochen!</p>
    </div>
  </div>

  <div class="panel panel--center">
    <div class="brand" style="margin-top:8px">
      <div class="brand-name"><span>karlabrettin</span><span class="dot"></span></div>
      <div class="brand-sub">Coaching für Mütter</div>
      <div class="brand-claim">Begleitung - Stärkung - Beratung</div>
    </div>
    <div class="contact">
      <div class="name">Karla Brettin</div>
      <div>Heilpraktikerin für Psychotherapie</div>
      <div>Geprüfte Psychologische Beraterin</div>
      <div class="gap">Telefon: 0171 482 36 510</div>
      <div>Email: info@karla-brettin.de</div>
      <div>www.karla-brettin.de</div>
      <div>Praxisgemeinschaft am Hain</div>
      <div>Lindenweg 14</div>
      <div>40999 Rheinau</div>
    </div>
    <div class="services">
      <h3>Weiteres Leistungsspektrum</h3>
      <div>Psychologische Beratung</div>
      <div>Stressbewältigung – Burnoutprävention</div>
      <div>Achtsamkeitstraining – Palmtherapy</div>
      <div>Lösungsfokussierte Kurzzeittherapie –</div>
      <div>Gewaltfreie Kommunikation –</div>
      <div>Energiearbeit – Geistiges Heilen – Reiki</div>
    </div>
  </div>

  <div class="panel panel--cover">
    <p class="quote"><span class="mark">”</span>Das Baby ist da und nichts ist mehr wie es war</p>
    <div class="photo photo--mother" role="img" aria-label="Foto: Mutter hält ihr schlafendes Neugeborenes an der Schulter"></div>
    <div class="brand brand--bottom">
      <div class="brand-name"><span>karlabrettin</span><span class="dot"></span></div>
      <div class="brand-sub">Coaching für Mütter</div>
      <div class="brand-claim">Begleitung - Stärkung - Beratung</div>
    </div>
  </div>
</section>

<section class="spread spread--inside" aria-label="Innenseite">
  <div class="panel panel--grey">
    <div class="section-label" style="margin-top:4px">Ihre <em>Situation</em></div>
    <ul class="bullets">
      <li>Haben Sie sich Ihr Mutterglück anders vorgestellt? - Sie hatten sich so auf Ihr Baby gefreut, aber die Realität ist gar nicht so, wie Sie sie sich das gedacht haben?</li>
      <li>Fühlen Sie sich isoliert: plötzlich sind Sie allein in Ihrem Zuhause mit Ihrem Kind, Ihre Kollegen und Freunde führen weiterhin Ihr früheres Leben – Sie sind aber nicht mehr mit dabei?</li>
      <li>Das Verständnis Ihrer Umgebung für Ihre neue Situation fehlt. Sogar die Partnerschaft ist plötzlich ganz anders als sie es vorher war?</li>
      <li>Der Fokus aller richtet sich fast ausschließlich auf Ihr Kind - doch wo bleiben Sie eigentlich?</li>
      <li>Sie werden nur noch als Mutter wahrgenommen - kaum mehr als die Frau und die Persönlichkeit, die Sie vorher waren und auch immer noch sind?</li>
      <li>Sie fühlen sich oft erschöpft, ratlos, überfordert, unverstanden?</li>
    </ul>
    <div class="photo photo--tired" role="img" aria-label="Foto: erschöpfte Mutter mit schlafendem Baby neben dem Kinderbett"></div>
  </div>

  <div class="panel panel--center support">
    <div class="section-label" style="margin-top:4px">Meine <em>Unterstützung</em></div>
    <div class="section-rule"></div>
    <h4>BEGLEITUNG</h4>
    <p>Die gute Nachricht: Sie müssen diese belastende Situation nicht allein bewältigen - erleben Sie Erleichterung, indem Sie sich von mir beraten lassen.</p>
    <p>Genießen SIE im Einzelcoaching, dass nur IHRE Situation zählt und SIE im Mittelpunkt stehen, denn als Coach gehe ich individuell auf Ihre Person und Situation ein.</p>
    <h4>STÄRKUNG</h4>
    <p>Verlagern Sie mit mir Ihren Fokus auf andere Sichtweisen und neue Wege. Entscheiden Sie sich für einen Weg, der zu Ihnen passt und Sie glücklich macht.<br>Finden Sie die Mutterrolle, die es Ihnen ermöglicht gut für sich zu sorgen und bei sich zu bleiben und leben Sie so Ihre Bedürfnisse und Interessen im Einklang mit denen Ihrer Familie.</p>
    <h4>BERATUNG</h4>
    <p>Trotz Unmengen an Informationen fühlen sich viele Mütter mit ihren Themen alleine, hilflos und überfordert.<br>Bei mir bleiben Sie nicht allein und ratlos: denn wir finden individuelle Antworten auf Ihre ganz persönlichen Fragen.<br>Sie geben dabei die Themen und das Tempo an - ich begleite Sie aufmerksam, achtsam und wertschätzend!</p>
  </div>

  <div class="panel way">
    <div class="section-label" style="margin-top:4px">Unser <em>Weg</em></div>
    <div class="section-rule" style="margin-left:0"></div>
    <p>Gemeinsam können wir Ihre Situation durchleuchten.</p>
    <h3>MEIN ANGEBOT UMFASST...</h3>
    <div class="offer"><svg width="7" height="7" viewBox="0 0 10 10"><circle cx="5" cy="5" r="5" fill="#555"/><path d="M5 2.5v5M2.5 5h5" stroke="#fff" stroke-width="1.4"/></svg>Einzelcoaching</div>
    <p>Sie können wählen: das Coaching kann in meiner Praxis in Rheinau oder gern auch bei Ihnen zu Hause stattfinden, so wie es gerade für Sie am besten passt.</p>
    <p>Die Zeit, die Sie und eventuell auch Ihr Partner sich für ein Coaching nehmen, ist überschaubar: maximal drei bis fünf Sitzungen à 60 Minuten können ausreichen, um Ihre momentane Situation anzuschauen und zu verändern.</p>
    <p>Wenn Einzelcoaching nicht das Richtige für Sie ist, können Sie sich auch für ein</p>
    <div class="offer"><svg width="7" height="7" viewBox="0 0 10 10"><circle cx="5" cy="5" r="5" fill="#555"/><path d="M5 2.5v5M2.5 5h5" stroke="#fff" stroke-width="1.4"/></svg>Gruppencoaching</div>
    <p>entscheiden. Lernen Sie dadurch Gleichgesinnte kennen und profitieren Sie in doppelter Hinsicht – nach dem Motto: „Lieber gemeinsam als einsam“.</p>
    <div class="offer"><svg width="7" height="7" viewBox="0 0 10 10"><circle cx="5" cy="5" r="5" fill="#555"/><path d="M5 2.5v5M2.5 5h5" stroke="#fff" stroke-width="1.4"/></svg>Telefoncoaching</div>
    <p>Sie bestimmen Ort und Zeit. Dieses Angebot könnte das Richtige für Sie sein, wenn Sie zeitlich oder örtlich gebunden sind.</p>
  </div>
</section>

</body>
</html>
```